Brindovalle Business cards

Dear team, I need to get the design file to suit it to our team. The focus of the business card is the Automotive Market and the design must be in black colour and the logo must be in glossy black. On the front of the card I need to get the following info:

- Name and Surname
- Title
- eMail
- Phone Number
- Skype account
- domain address

```html
<!DOCTYPE html>
<html lang="es">
<head>
<meta charset="utf-8">
<title>Brindovalle – Business cards</title>
<link href="https://fonts.googleapis.com/css2?family=Montserrat:wght@400;500;700;800&display=swap" rel="stylesheet">
<style>
  :root {
    --page-bg: #1b1b1b;
    --card-bg: #262626;
    --card-back-bg: #1f1f1f;
    --swoosh: #3a3a3a;
    --swoosh-edge: #6a6a6a;
    --red: #e1262a;
    --white: #ffffff;
    --muted: #e6e6e6;
  }
  html, body {
    margin: 0;
    width: 1200px;
    height: 1186px;
    overflow: hidden;
    background: var(--page-bg);
    font-family: "Montserrat", sans-serif;
  }
  .card {
    position: absolute;
    left: 130px;
    width: 940px;
    height: 520px;
    border-radius: 34px;
    overflow: hidden;
    box-shadow: 0 18px 40px rgba(0,0,0,.55);
  }
  .card-back {
    top: 50px;
    background: var(--card-back-bg);
  }
  .back-pattern {
    position: absolute;
    inset: 0;
    background: linear-gradient(135deg, #4a4a4a 0%, #2a2a2a 45%, #1c1c1c 100%);
  }
  .card-front {
    top: 616px;
    background: var(--card-bg);
  }
  .front-swoosh {
    position: absolute;
    left: 0; top: 0;
    width: 940px; height: 520px;
  }
  .wheel-area {
    position: absolute;
    left: 620px; top: 20px;
    width: 200px; height: 200px;
    border-radius: 50%;
    background: radial-gradient(circle at 40% 35%, #4a4a4a 0%, #2b2b2b 60%, #202020 100%);
  }
  .brand {
    position: absolute;
    left: 56px; top: 200px;
    display: flex;
    align-items: center;
    gap: 16px;
  }
  .brand-square {
    width: 44px; height: 44px;
    background: var(--red);
  }
  .brand-name {
    color: var(--white);
    font-weight: 700;
    font-size: 50px;
    letter-spacing: -0.5px;
  }
  .divider {
    position: absolute;
    left: 56px; top: 330px;
    width: 830px; height: 2px;
    background: var(--red);
  }
  .person-name {
    position: absolute;
    left: 56px; top: 286px;
    margin: 0;
    color: var(--red);
    font-weight: 800;
    font-size: 30px;
    letter-spacing: 0.5px;
    text-transform: uppercase;
  }
  .person-title {
    position: absolute;
    left: 56px; top: 342px;
    margin: 0;
    color: var(--white);
    font-weight: 500;
    font-size: 19px;
  }
  .contacts {
    position: absolute;
    left: 56px; top: 382px;
    margin: 0; padding: 0;
    list-style: none;
  }
  .contacts li {
    display: flex;
    align-items: center;
    gap: 14px;
    height: 30px;
    color: var(--muted);
    font-size: 18px;
    font-weight: 400;
  }
  .contacts svg { width: 16px; height: 16px; flex: none; }
  .address {
    position: absolute;
    right: 54px; top: 350px;
    margin: 0;
    text-align: right;
    color: var(--muted);
    font-size: 17px;
    line-height: 1.35;
    font-style: normal;
  }
</style>
</head>
<body>

<section class="card card-back" aria-label="Card back">
  <div class="back-pattern" role="img" aria-label="Repeating glossy black brand pattern with one red accent tile"></div>
</section>

<section class="card card-front" aria-label="Card front">
  <svg class="front-swoosh" viewBox="0 0 940 520" aria-hidden="true">
    <defs>
      <linearGradient id="swooshGrad" x1="0" y1="0" x2="1" y2="1">
        <stop offset="0" stop-color="#4a4a4a"/>
        <stop offset="1" stop-color="#2c2c2c"/>
      </linearGradient>
    </defs>
    <path d="M470 0 H940 V250 C900 110 780 40 620 50 C560 54 510 30 470 0 Z" fill="url(#swooshGrad)"/>
    <path d="M940 250 C900 110 780 40 620 50" fill="none" stroke="var(--swoosh-edge)" stroke-width="2"/>
  </svg>
  <div class="wheel-area" role="img" aria-label="Large glossy black brand symbol"></div>

  <div class="brand">
    <span class="brand-square"></span>
    <span class="brand-name">Brindovalle</span>
  </div>

  <h1 class="person-name">Marco Ferrati</h1>
  <div class="divider"></div>
  <p class="person-title">Comercial</p>

  <ul class="contacts">
    <li>
      <svg viewBox="0 0 16 16"><path fill="#e1262a" d="M3 1h3l1.5 4-2 1.3a9 9 0 0 0 4.2 4.2L11 8.5l4 1.5v3a2 2 0 0 1-2 2A12 12 0 0 1 1 3a2 2 0 0 1 2-2z"/></svg>
      612 40 27 58
    </li>
    <li>
      <svg viewBox="0 0 16 16"><rect x="1" y="3" width="14" height="10" rx="1.5" fill="#e1262a"/><path d="M1.5 4 8 9l6.5-5" fill="none" stroke="#262626" stroke-width="1.4"/></svg>
      redazione@brindovalle.com
    </li>
    <li>
      <svg viewBox="0 0 16 16"><circle cx="8" cy="8" r="7" fill="#e1262a"/></svg>
      @brindovalle
    </li>
    <li>
      <svg viewBox="0 0 16 16"><circle cx="8" cy="8" r="6.5" fill="none" stroke="#e1262a" stroke-width="1.6"/><ellipse cx="8" cy="8" rx="2.8" ry="6.5" fill="none" stroke="#e1262a" stroke-width="1.4"/><path d="M1.5 8h13" stroke="#e1262a" stroke-width="1.4"/></svg>
      www.brindovalle.com
    </li>
  </ul>

  <address class="address">Pol. Ind. Norvale, C/4 nº 22<br>41820 Villanueva del Prado</address>
</section>

</body>
</html>
```